NZ First of it's kind solutions directory and marketplace for busy Mums needs a business card design

We need a business card design for our new nationwide business in NZ (long term plans to go global). We provide solutions to the everyday challenges that busy Mums face by connecting them with quality communities and suppliers of carefully selected, relevant products and services. We sell direct via our online marketplace. The final design should communicate our values of inclusivity, quality and smart solutions. Colours should incorporate our logo colour palette of #477077 and #6ba8b2. Our website is at https://www.brightnestmums.example

Target Market(s)

busy Mums, Age 28 – 50, female, income over $100K, location main centres NZ primarily but NZ wide. Is likely juggling work or career with a young family. Probably had hobbies which have fallen by the wayside.
-Wants to succeed in her chosen career without compromising on family life
-to successfully juggle her career without feeling like she is compromising her children
- Is time poor, something always has to give and it’s generally her health (she’ll stay up late, get stressed)
- probably ex corporate or professional career. Has discretional income

Industry/Entity Type

Business

Contact Information for Business Card

Lena Forbisher, Founder, BrightNestMums.example (Strapline Tap; Gather; Sorted), 47 Kowhai Terrace, Ellerslie, Auckland 1051, New Zealand. Mob: 021 483 517 Ph: +64 (0)9 571 4860

Font styles to use
Other font styles liked:
• Raleway, and/or Architects Daughter

Colors
00a990
33b8a4
86cfc6
cfeae6

Requirements
Must have
• the above details, streamline. the logo and colours associated with those logos
Should not have
• foil or metallic colours

```html
<!DOCTYPE html>
<html lang="en">
<head>
<meta charset="utf-8">
<title>BrightNestMums – Business Card</title>
<link href="https://fonts.googleapis.com/css2?family=Roboto:wght@400;500&family=Roboto+Condensed:wght@400;700&display=swap" rel="stylesheet">
<style>
  :root {
    --backdrop: #262626;
    --teal-deep: #477077;
    --teal-light: #6ba8b2;
    --swoosh-grey: #575757;
    --paper: #f2f2f2;
    --ink: #4a4a4a;
    --white: #ffffff;
  }
  * { margin: 0; padding: 0; box-sizing: border-box; }
  html, body {
    width: 1200px; height: 960px; overflow: hidden;
    background: var(--backdrop);
  }
  .card {
    position: absolute; width: 600px; height: 342px; overflow: hidden;
    box-shadow: 0 3px 8px rgba(0,0,0,.55);
  }
  .card--front { left: 314px; top: 113px; background: var(--paper); }
  .card--back { left: 311px; top: 472px; background: var(--teal-light); }

  .front-waves { position: absolute; inset: 0; }

  .person {
    position: absolute; right: 28px; top: 26px; text-align: right;
    font-family: "Roboto Condensed", sans-serif; color: var(--white);
  }
  .person__name { font-size: 22px; font-weight: 700; letter-spacing: .2px; line-height: 1.1; }
  .person__role { font-size: 15px; font-weight: 400; letter-spacing: .5px; margin-top: 2px; }

  .brand {
    position: absolute; left: 28px; top: 178px;
    display: flex; align-items: center; gap: 10px;
  }
  .brand__dot { width: 16px; height: 16px; border-radius: 50%; background: var(--teal-deep); }
  .brand__name {
    font-family: "Roboto", sans-serif; font-weight: 500; font-size: 29px;
    color: var(--teal-deep); letter-spacing: -.3px;
  }

  .contact, .address {
    position: absolute; font-family: "Roboto", sans-serif; font-size: 14.5px;
    color: var(--ink); line-height: 19.5px;
  }
  .contact { left: 27px; top: 262px; list-style: none; }
  .contact li { display: flex; align-items: center; gap: 8px; }
  .contact svg { width: 13px; height: 13px; fill: var(--teal-deep); flex: none; }
  .address { right: 28px; top: 265px; text-align: right; font-style: normal; }

  .back-name {
    position: absolute; left: 0; right: 0; top: 132px; text-align: center;
    font-family: "Roboto", sans-serif; font-weight: 500; font-size: 40px;
    color: var(--white);
  }
  .strapline {
    position: absolute; left: 0; right: 0; top: 305px; text-align: center;
    font-family: "Roboto", sans-serif; font-size: 14.5px; color: var(--white);
  }
</style>
</head>
<body>

<section class="card card--front">
  <svg class="front-waves" viewBox="0 0 600 342" aria-hidden="true">
    <rect width="600" height="342" fill="var(--teal-deep)"/>
    <path d="M0,118 C70,40 170,10 290,55 C400,96 500,104 600,88 L600,342 L0,342 Z" fill="var(--white)"/>
    <path d="M0,126 C70,48 170,18 290,63 C400,104 500,112 600,96 L600,342 L0,342 Z" fill="var(--teal-light)"/>
    <path d="M0,137 C70,60 170,30 290,75 C400,116 500,122 600,104 L600,342 L0,342 Z" fill="var(--white)"/>
    <path d="M0,142 C25,85 100,40 170,46 C210,49 240,60 262,78 C230,60 190,52 150,58 C80,70 30,110 0,145 Z" fill="var(--swoosh-grey)"/>
    <path d="M0,140 C70,64 170,34 290,79 C400,120 500,126 600,108 L600,342 L0,342 Z" fill="var(--paper)"/>
  </svg>

  <div class="person">
    <div class="person__name">LENA FORBISHER</div>
    <div class="person__role">FOUNDER</div>
  </div>

  <div class="brand">
    <span class="brand__dot"></span>
    <span class="brand__name">BrightNestMums</span>
  </div>

  <ul class="contact">
    <li>
      <svg viewBox="0 0 24 24"><path d="M6.6 10.8a15.1 15.1 0 0 0 6.6 6.6l2.2-2.2c.3-.3.7-.4 1-.2 1.1.4 2.3.6 3.6.6.6 0 1 .4 1 1V20c0 .6-.4 1-1 1A17 17 0 0 1 3 4c0-.6.4-1 1-1h3.5c.6 0 1 .4 1 1 0 1.3.2 2.5.6 3.6.1.3 0 .7-.2 1z"/></svg>
      +64 (0)9 571 4860
    </li>
    <li>
      <svg viewBox="0 0 24 24"><path d="M7 1h10a2 2 0 0 1 2 2v18a2 2 0 0 1-2 2H7a2 2 0 0 1-2-2V3a2 2 0 0 1 2-2zm0 3v14h10V4zm5 15.5a1.2 1.2 0 1 0 0 2.4 1.2 1.2 0 0 0 0-2.4z"/></svg>
      021 483 517
    </li>
    <li>
      <svg viewBox="0 0 24 24"><path d="M12 2a10 10 0 1 0 0 20 10 10 0 0 0 0-20zm-1 17.9A8 8 0 0 1 4.2 10.2L9 15v1a2 2 0 0 0 2 2zm6.9-2.5A2 2 0 0 0 16 16h-1v-3a1 1 0 0 0-1-1H8v-2h2a1 1 0 0 0 1-1V7h2a2 2 0 0 0 2-2v-.4a8 8 0 0 1 2.9 12.8z"/></svg>
      BrightNestMums.example
    </li>
  </ul>

  <address class="address">
    47 Kowhai Terrace<br>
    Ellerslie, Auckland<br>
    1051, New Zealand
  </address>
</section>

<section class="card card--back">
  <div class="back-name">BrightNestMums</div>
  <p class="strapline">Tap; Gather; Sorted</p>
</section>

</body>
</html>
```